Website Creation for Kesto Course 2025 by Lon Varick "The Girl Who Painted Her Sky"

Project Title: "Kesto" Course Design Brief – Website design Build on Tilda
Client: Pebble Lantern Education
Course Title: Kesto by Lon Varick – The Girl Who Painted Her Sky
Logo: Lon Varick Logo
Course price: TBA
Overview:
We are seeking a designer to create cohesive and professional design assets for a new online course called Kesto. This transformative program combines neuroscience, emotional wellness, and ancient meditation practices to guide users through a journey of self-healing. We want the design to feel scientific yet spiritual, with clean, modern aesthetics that also convey depth and transformation. We use Tilda as our website builder so we need a design that can be easily transposed to that platform.
We require a visually compelling and dynamic banner image for the course webpage hero section (desktop and mobile versions)
We also require 7 x Individual thumbnail designs for each chakra meditation that will accompany the course with a workbook that will be designed in house (aligned with energy centre themes / Solfeggio frequencies / cosmic and sacred geometry)
Visual Direction:
• Clean, modern design with dark elements that balance science and spirituality.
• Soft gradients, energetic colors for chakras, and subtle abstract patterns or sacred geometry.
• Imagery could include brain neural networks, energy centres, or serene meditative figures and sacred geometry.
Course Themes to Inspire Design:
• Neuroplasticity and brain rewiring
• Emotional trauma and healing
• Meditation and Solfeggio frequencies
• Mind-body-spirit connection
• Empowerment and transformation
Lesson Breakdown:
• Lesson 1: The Science of Meditation & the Mind-Body Connection
• Lesson 2: Lon Varick’s Personal Healing & Neuroplasticity
• Lesson 3: Emotional Stress and Disease
• Lesson 4: ZRM (Zonal Ribbon Merge) Process
• Lesson 5: Solfeggio Frequencies & Chakra Healing
Target Audience:
Adult women 40 to 60 years old interested in healing illness, improving mental health, improving relationships, improving personal development, alternative healing, and meditation.

self development, meditation, healing

1 page

• futurapt

• branding copy used with relevant imagery and brand colours Stone #FAF0EA Sand #E2B9A5 Steel Blue #4F5266 Navy #2B243A Black: #000000 and Futura PT font
• chakra symbols and cosmic aesthetics with informational psychographics
• bright bold colours that don't match our branding

```html
<!DOCTYPE html>
<html lang="en">
<head>
<meta charset="UTF-8">
<title>Kesto by Lon Varick – The Girl Who Painted Her Sky</title>
<link rel="stylesheet" href="https://fonts.googleapis.com/css2?family=Montserrat:wght@300;400;500;600;700&family=Nunito+Sans:wght@400;600;700&display=swap">
<style>
:root{
  --ink:#111111;
  --body:#555555;
  --white:#ffffff;
  --grey-band:#eeeeee;
  --purple:#7a0bbd;
  --magenta:#c2147f;
  --violet:#8d12c9;
  --lilac:#ece2f7;
  --pink-soft:#f6dcec;
  --black:#000000;
}
*{margin:0;padding:0;box-sizing:border-box}
html,body{width:1200px;height:4918px;overflow:hidden}
body{position:relative;background:var(--white);font-family:"Nunito Sans",Arial,sans-serif;color:var(--ink)}
.abs{position:absolute}
.section{position:absolute;left:0;width:1200px}
.btn{position:absolute;display:flex;align-items:center;justify-content:center;color:var(--white);font-family:"Montserrat",sans-serif;font-weight:700;font-size:15px;letter-spacing:.3px;background:linear-gradient(90deg,var(--purple),var(--magenta));clip-path:polygon(7% 0,93% 0,100% 50%,93% 100%,7% 100%,0 50%)}
.heading{font-family:"Montserrat",sans-serif;font-weight:400;font-size:32px;letter-spacing:.3px}
.heading b{font-weight:700}
.center{text-align:center;left:0;width:1200px}

/* hero */
.hero{top:0;height:687px;background:linear-gradient(120deg,#16235a 0%,#0d1437 50%,#070b22 100%)}
.hero-visual{left:640px;top:0;width:560px;height:687px;background:linear-gradient(160deg,#8a2fd0 0%,#3f37c4 35%,#18307e 70%,#0d1437 100%)}
.nav a{position:absolute;top:42px;color:var(--white);font-family:"Montserrat",sans-serif;font-size:15px;font-weight:500;text-decoration:none;letter-spacing:.3px}
.nav .active{font-weight:700}
.brand{left:540px;top:14px;width:120px;height:96px;display:flex;flex-direction:column;align-items:center;justify-content:center;color:var(--white);font-family:"Montserrat",sans-serif;font-weight:600;font-size:12px;letter-spacing:2px}
.brand .dot{width:46px;height:46px;border:1.5px solid rgba(255,255,255,.7);border-radius:50%;margin-bottom:8px}
.social span{position:absolute;width:25px;height:25px;border-radius:50%;background:var(--violet)}
.hero-badge{left:113px;top:174px;height:32px;padding:0 20px;border-radius:16px;background:#4a0a49;color:var(--white);font-size:16px;font-weight:600;display:flex;align-items:center;font-family:Arial,sans-serif}
.hero-kicker{left:113px;top:228px;color:var(--white);font-family:Arial,sans-serif;font-weight:700;font-size:25px}
.hero-title{left:109px;top:268px;color:var(--white);font-family:"Montserrat",sans-serif;font-size:44px;line-height:52px;font-weight:300;width:560px}
.hero-title b{font-weight:700}
.hero-copy{left:113px;top:432px;width:450px;color:var(--white);font-family:Arial,sans-serif;font-size:16.5px;line-height:31px}

/* about */
.about{top:687px;height:607px}
.about-title{left:111px;top:785px}
.about-copy{left:111px;width:470px;font-size:14.5px;line-height:27.5px;color:var(--body)}
.photo{position:absolute}

/* chakra */
.chakras{top:1294px;height:807px;background:var(--grey-band)}
.chakra{position:absolute;width:300px;text-align:center}
.chakra .orb{width:104px;height:104px;border-radius:50%;margin:0 auto;display:flex;align-items:center;justify-content:center}
.chakra .orb i{display:block;width:40px;height:40px;border-radius:50%}
.chakra h3{margin-top:34px;font-family:"Montserrat",sans-serif;font-weight:600;font-size:16px;letter-spacing:.3px}
.chakra p{margin:8px auto 0;width:240px;font-size:14.5px;line-height:25.5px;color:var(--body)}
.divider{position:absolute;width:1px;background:#d6d6d6}

/* motivation */
.motivation{top:2101px;height:496px;background:linear-gradient(180deg,#1c1a16 0%,#141211 55%,#090909 100%)}

/* lessons */
.lessons{top:2597px;height:798px}
.lesson{position:absolute;left:111px}
.lesson .tick{position:absolute;left:0;top:0;width:64px;height:64px;border-radius:50%;background:linear-gradient(135deg,var(--purple),var(--magenta));display:flex;align-items:center;justify-content:center}
.lesson h4{position:absolute;left:103px;top:-3px;font-family:"Montserrat",sans-serif;font-weight:700;font-size:18px;white-space:nowrap}
.lesson p{position:absolute;left:103px;top:27px;font-size:16px;white-space:nowrap;color:#333}

/* reviews */
.reviews{top:3395px;height:590px;background:var(--grey-band)}
.avatar{position:absolute;width:126px;height:126px;border-radius:50%}
.review{position:absolute;width:310px}
.review p{font-size:14.5px;line-height:25.5px;color:#444}
.review h5{margin-top:14px;font-family:"Montserrat",sans-serif;font-weight:600;font-size:16.5px}

/* contact */
.contact{top:3985px;height:474px;background:linear-gradient(180deg,#12232b 0%,#0d1a20 60%,#071015 100%)}
.field{position:absolute;top:4286px;height:47px;border:1.5px solid #cfd4d8;color:var(--white);font-size:15px;padding-left:20px;display:flex;align-items:center}
.submit{position:absolute;top:4286px;left:908px;width:142px;height:47px;background:linear-gradient(90deg,var(--purple),var(--magenta));color:var(--white);font-family:"Montserrat",sans-serif;font-weight:700;font-size:16px;display:flex;align-items:center;justify-content:center}

/* footer */
.footer-line{position:absolute;text-align:center;left:0;width:1200px;font-family:"Montserrat",sans-serif}
.copyright{top:4864px;height:54px;background:var(--black);color:var(--white);display:flex;align-items:center;justify-content:center;font-family:"Montserrat",sans-serif;font-size:14px;font-weight:500}
</style>
</head>
<body>

<!-- HERO -->
<header class="section hero">
  <div class="abs hero-visual" role="img" aria-label="Glowing neural network brain inside a translucent human head profile"></div>
  <nav class="nav">
    <a class="active" href="#" style="left:113px">HOME</a>
    <a href="#" style="left:191px">ABOUT US</a>
    <a href="#" style="left:303px">SERVICES</a>
    <a href="#" style="left:410px">CONTACTS</a>
  </nav>
  <div class="abs brand"><span class="dot"></span>LON VARICK</div>
  <div class="social" aria-label="Social media links">
    <span style="left:938px;top:40px"></span>
    <span style="left:978px;top:40px"></span>
    <span style="left:1018px;top:40px"></span>
    <span style="left:1060px;top:40px"></span>
  </div>
  <div class="abs hero-badge">Course price: TBA</div>
  <div class="abs hero-kicker">Pebble Lantern Education</div>
  <h1 class="abs hero-title">Kesto by Lon Varick – <b>The<br>Girl Who Painted<br>Her Sky</b></h1>
  <p class="abs hero-copy">Lorem ipsum dolor sit amet, consectetur adipiscing elit, sed do eiusmod tempor incididunt ut labore et dolore magna aliqua.</p>
  <a class="btn" style="left:113px;top:542px;width:162px;height:45px">GET STARTED</a>
  <svg class="abs" style="left:580px;top:594px" width="40" height="24" viewBox="0 0 40 24"><polyline points="2,3 20,21 38,3" fill="none" stroke="#ffffff" stroke-width="3"/></svg>
</header>

<!-- ABOUT -->
<section class="section about"></section>
<h2 class="abs heading about-title"><b>ABOUT</b> US</h2>
<p class="abs about-copy" style="top:848px">At vero eos et accusamus et iusto odio dignissimos ducimus qui blanditiis praesentium voluptatum deleniti atque corrupti quos dolores et quas molestias excepturi sint occaecati cupiditate non provident, similique sunt in culpa qui officia deserunt mollitia animi, id est laborum et dolorum fuga.</p>
<p class="abs about-copy" style="top:1014px">Et harum quidem rerum facilis est et expedita distinctio. Nam libero tempore, cum soluta nobis est eligendi optio cumque nihil impedit quo minus id quod maxime possimus,</p>
<a class="btn" style="left:111px;top:1130px;width:156px;height:50px">READ MORE</a>
<div class="photo" style="left:630px;top:788px;width:218px;height:190px;background:linear-gradient(160deg,#7a2fc8,#1c1a5a)" role="img" aria-label="Glowing purple brain illustration"></div>
<div class="photo" style="left:872px;top:788px;width:218px;height:190px;background:linear-gradient(160deg,#8a5a5e,#2a1a24)" role="img" aria-label="Sacred geometry pattern with soft coloured lights"></div>
<div class="photo" style="left:630px;top:998px;width:218px;height:190px;background:linear-gradient(160deg,#b8bec4,#4e5d6a)" role="img" aria-label="Therapist helping an older woman with an exercise ball"></div>
<div class="photo" style="left:872px;top:998px;width:218px;height:190px;background:linear-gradient(180deg,#3a1f0e,#c27428)" role="img" aria-label="Person meditating among candles"></div>

<!-- CHAKRAS -->
<section class="section chakras"></section>
<h2 class="abs heading center" style="top:1378px">CHAKRA <b>MEDITATION THUMBNAILS</b></h2>
<div class="divider" style="left:416px;top:1480px;height:190px"></div>
<div class="divider" style="left:794px;top:1480px;height:190px"></div>
<div class="divider" style="left:416px;top:1765px;height:210px"></div>
<div class="divider" style="left:794px;top:1765px;height:210px"></div>

<div class="chakra" style="left:77px;top:1455px">
  <div class="orb" style="background:#f7dede"><i style="background:#d8283a" role="img" aria-label="Root chakra symbol"></i></div>
  <h3>ROOT CHAKRA</h3>
  <p>Excepteur sint occaecat cupidatat officia deserunt mollit anim id est laborum.</p>
</div>
<div class="chakra" style="left:450px;top:1455px">
  <div class="orb" style="background:#f8e2d6"><i style="background:#d4672a" role="img" aria-label="Sacral chakra symbol"></i></div>
  <h3>SACRAL CHAKRA</h3>
  <p>Excepteur sint occaecat cupidatat officia deserunt mollit anim id est laborum.</p>
</div>
<div class="chakra" style="left:821px;top:1455px">
  <div class="orb" style="background:#f8eed3"><i style="background:#e0a814" role="img" aria-label="Solar plexus chakra symbol"></i></div>
  <h3>SOLAR PLEXUS</h3>
  <p>Excepteur sint occaecat cupidatat officia deserunt mollit anim id est laborum.</p>
</div>
<div class="chakra" style="left:77px;top:1742px">
  <div class="orb" style="background:#dcefe1"><i style="background:#1c9a4c" role="img" aria-label="Heart chakra symbol"></i></div>
  <h3>HEART CHAKRA</h3>
  <p>Excepteur sint occaecat cupidatat officia deserunt mollit anim id est laborum.</p>
</div>
<div class="chakra" style="left:450px;top:1742px">
  <div class="orb" style="background:#d9eef4"><i style="background:#1c93c4" role="img" aria-label="Throat chakra symbol"></i></div>
  <h3>THROAT CHAKRA</h3>
  <p>Excepteur sint occaecat cupidatat officia deserunt mollit anim id est laborum.</p>
</div>
<div class="chakra" style="left:821px;top:1742px">
  <div class="orb" style="background:#e6dcf3"><i style="background:#7a3cb8" role="img" aria-label="Third eye chakra symbol"></i></div>
  <h3>THIRD EYE CHAKRA</h3>
  <p>Excepteur sint occaecat cupidatat officia deserunt mollit anim id est laborum.</p>
</div>

<!-- MOTIVATION -->
<section class="section motivation" role="img" aria-label="Dark mountain landscape with faint sacred geometry"></section>
<h2 class="abs heading center" style="top:2235px;color:#fff">ADD A <b>MOTIVATIONAL PHRASE</b></h2>
<p class="abs center" style="top:2298px;color:#fff;font-size:16px;line-height:29px">Duis aute irure dolor in reprehenderit in voluptate velit esse cillum dolore eu fugiat nulla pariatur.<br>Excepteur sint occaecat cupidatat non proident, sunt in culpa qui officia deserunt mollit anim id est laborum.</p>
<svg class="abs" style="left:410px;top:2370px" width="64" height="60" viewBox="0 0 64 60"><path d="M6 4 C 8 34, 30 50, 56 48" fill="none" stroke="#ffffff" stroke-width="2"/><polyline points="46,40 57,48 46,55" fill="none" stroke="#ffffff" stroke-width="2"/></svg>
<a class="btn" style="left:506px;top:2411px;width:188px;height:46px">CALL TO ACTION</a>

<!-- LESSONS -->
<section class="section lessons"></section>
<h2 class="abs heading" style="left:111px;top:2690px">OUR <b>LESSON</b></h2>
<p class="abs" style="left:111px;top:2746px;font-size:16px;line-height:27px;color:#333">Duis aute irure dolor in reprehenderit in voluptate velit esse cillum dolore eu fugiat nulla pariatur.<br>Excepteur sint occaecat cupidatat non proident</p>

<div class="lesson" style="top:2836px"><div class="tick"><svg width="30" height="22" viewBox="0 0 30 22"><polyline points="3,11 11,19 27,3" fill="none" stroke="#fff" stroke-width="3.5"/></svg></div><h4>Lesson 1:</h4><p>The Science of Meditation &amp; the Mind-Body Connection</p></div>
<div class="lesson" style="top:2932px"><div class="tick"><svg width="30" height="22" viewBox="0 0 30 22"><polyline points="3,11 11,19 27,3" fill="none" stroke="#fff" stroke-width="3.5"/></svg></div><h4>Lesson 2:</h4><p>Lon Varick’s Personal Healing &amp; Neuroplasticity</p></div>
<div class="lesson" style="top:3029px"><div class="tick"><svg width="30" height="22" viewBox="0 0 30 22"><polyline points="3,11 11,19 27,3" fill="none" stroke="#fff" stroke-width="3.5"/></svg></div><h4>Lesson 3:</h4><p>Emotional Stress and Disease</p></div>
<div class="lesson" style="top:3124px"><div class="tick"><svg width="30" height="22" viewBox="0 0 30 22"><polyline points="3,11 11,19 27,3" fill="none" stroke="#fff" stroke-width="3.5"/></svg></div><h4>Lesson 4:</h4><p>ZRM (Zonal Ribbon Merge) Process</p></div>
<div class="lesson" style="top:3220px"><div class="tick"><svg width="30" height="22" viewBox="0 0 30 22"><polyline points="3,11 11,19 27,3" fill="none" stroke="#fff" stroke-width="3.5"/></svg></div><h4>Lesson 5:</h4><p>Solfeggio Frequencies &amp; Chakra Healing</p></div>

<div class="abs" style="left:784px;top:2824px;width:336px;height:324px;border-radius:12px;background:linear-gradient(160deg,var(--lilac),var(--pink-soft))"></div>
<div class="abs" style="left:674px;top:2856px;width:416px;height:424px;border-radius:12px;background:linear-gradient(160deg,#3a1c4e 0%,#6a2150 50%,#2a1538 100%)" role="img" aria-label="Sacred geometry star with lotus flower"></div>

<!-- REVIEWS -->
<section class="section reviews"></section>
<h2 class="abs heading center" style="top:3477px">CLIENT <b>REVIEWS</b></h2>

<div class="avatar" style="left:111px;top:3564px;background:linear-gradient(160deg,#b9a898,#4e4640)" role="img" aria-label="Client portrait"></div>
<div class="review" style="left:261px;top:3556px"><p>Duis aute irure dolor in reprehenderit in voluptate velit esse cillum dolore eu fugiat nulla pariatur.</p><h5>Mira Tovald</h5></div>

<div class="avatar" style="left:647px;top:3564px;background:linear-gradient(160deg,#e0d4c6,#9c7656)" role="img" aria-label="Client portrait"></div>
<div class="review" style="left:797px;top:3556px"><p>Duis aute irure dolor in reprehenderit in voluptate velit esse cillum dolore eu fugiat nulla pariatur.</p><h5>Jo Pellant</h5></div>

<div class="avatar" style="left:111px;top:3751px;background:linear-gradient(160deg,#b48a74,#3e2c28)" role="img" aria-label="Client portrait"></div>
<div class="review" style="left:261px;top:3743px"><p>Duis aute irure dolor in reprehenderit in voluptate velit esse cillum dolore eu fugiat nulla pariatur.</p><h5>Dana Quill</h5></div>

<div class="avatar" style="left:647px;top:3751px;background:linear-gradient(160deg,#c4c8cc,#6c7680)" role="img" aria-label="Client portrait"></div>
<div class="review" style="left:797px;top:3743px"><p>Duis aute irure dolor in reprehenderit in voluptate velit esse cillum dolore eu fugiat nulla pariatur.</p><h5>Rhea Sonnet</h5></div>

<!-- CONTACT -->
<section class="section contact" role="img" aria-label="Dark teal background with faint sacred geometry"></section>
<h2 class="abs heading center" style="top:4108px;color:#fff;font-weight:700">CONTACT US</h2>
<p class="abs" style="left:195px;top:4166px;width:810px;text-align:center;color:#fff;font-size:15.5px;line-height:27px">Duis aute irure dolor in reprehenderit in voluptate velit esse cillum dolore eu fugiat nulla pariatur. Excepteur sint occaecat cupidatat non proidentDuis aute irure dolor in reprehenderit in voluptate velit esse cillum dolore eu fugiat nulla pariatur. Excepteur sint occaecat cupidatat non proident</p>
<div class="field" style="left:147px;width:236px">Name</div>
<div class="field" style="left:399px;width:236px">Email</div>
<div class="field" style="left:651px;width:236px">Phone</div>
<div class="submit">SUBMIT</div>

<!-- FOOTER -->
<div class="footer-line" style="top:4548px;font-size:19px;font-weight:600">FEEL FREE TO CONTACT US</div>
<div class="footer-line" style="top:4604px;font-size:31px;font-weight:600">+1-555-014-2760</div>
<div class="footer-line" style="top:4650px;font-size:31px;font-weight:600">HELLO@PEBBLELANTERN.TEST</div>
<div class="footer-line" style="top:4729px;font-size:15px;font-weight:500">FOLLOW US ON SOCIAL MEDIA</div>
<div class="social" aria-label="Social media links">
  <span style="left:526px;top:4771px"></span>
  <span style="left:568px;top:4771px"></span>
  <span style="left:608px;top:4771px"></span>
  <span style="left:650px;top:4771px"></span>
</div>
<footer class="section copyright">COPYRIGHTS@2025.COMPANY NAME.ALL RIGHTS RESERVED</footer>

</body>
</html>
```